Flyer for Compassion training days

I need a A5-size, single-sided flyer design for my training days. They are weekends in a blend of Compassionate Communication and Buddhist teachings called Gentlewise Dialogue. The logo for Gentlewise that should be included.
The flyer needs room for 1) course title, 2) course dates, location & price, 3) course description, 4) booking info, 5) my picture & short bio, and 6) the gentlewise.co website (yes, it is 'co' and not 'com).
Updates

Target Market(s)

Women 35-65 years, well-educated, spiritually minded. May have interests like yoga and meditation.

Industry/Entity Type

Health And Wellness

Font styles to use
Sans Serif
Other font styles liked:
• Blue Plaque, Josefina are both great

Colors
fbf289
fdf9cf
cfeae6
33b8a4

Requirements
Must have
• The Gentlewise logo; my picture.
• Elegance. Calm and expansive feel.
• The poster provided in the project files shows you the kind of information I need to include.
• Colours -- greens and yellows, but the options on craft plaza are not quite the right shades.
• The logo colour can be changed.
Nice to have
• Classy (but not cliche) image associated with Buddhism; gentle curves similar to those on the business card (see project files).
Should not have
• Dark background. Busy, loud design. Overly 'swirly' design. Images that I have to buy separately.

```html
<!DOCTYPE html>
<html lang="en">
<head>
<meta charset="utf-8">
<title>Gentlewise Dialogue Core Course</title>
<link href="https://fonts.googleapis.com/css2?family=Lato:wght@300;400&family=Noto+Serif:ital,wght@0,700;1,400&display=swap" rel="stylesheet">
<style>
  :root {
    --backdrop: #ecebe8;
    --paper: #ffffff;
    --ink-brown: #4d4136;
    --olive: #7b6422;
    --body-grey: #6f6f6f;
    --text-dark: #3f3f3f;
    --green: #6dbb45;
    --green-light: #c3e1ae;
    --pill: #dcefd3;
    --sand-1: #f3f2ef;
    --sand-2: #d9d7d2;
  }
  * { margin: 0; padding: 0; box-sizing: border-box; }
  html, body { width: 941px; height: 1200px; overflow: hidden; background: var(--backdrop); }
  .flyer {
    position: absolute; left: 49px; top: 0;
    width: 872px; height: 1242px;
    background: var(--paper);
    transform: scale(0.9662); transform-origin: top left;
    font-family: "Lato", sans-serif; font-weight: 300;
    overflow: hidden;
  }
  .hero-image {
    position: absolute; left: 0; top: 0; width: 872px; height: 580px;
    background: radial-gradient(ellipse at 32% 52%, var(--sand-2) 0%, #e6e4e0 30%, var(--sand-1) 62%, #fbfbfa 100%);
  }
  .hero-curve { position: absolute; left: 0; top: 340px; width: 872px; height: 240px; }
  .headline {
    position: absolute; left: 395px; width: 450px; top: 58px; text-align: center;
    font-family: "Noto Serif", serif; color: var(--ink-brown);
  }
  .headline .equation { font-weight: 700; font-size: 24px; line-height: 30px; }
  .headline .course-title { font-style: italic; font-weight: 400; color: var(--olive); font-size: 38px; line-height: 44px; margin-top: 14px; }
  .headline .details { font-weight: 700; font-size: 19px; line-height: 25px; margin-top: 22px; }
  .brand-mark {
    position: absolute; left: 30px; top: 632px; display: flex; align-items: center; gap: 8px;
    font-family: "Lato", sans-serif; font-weight: 400; font-size: 20px; color: var(--green);
  }
  .brand-mark .dot { width: 18px; height: 18px; border-radius: 50%; background: var(--green); }
  .intro {
    position: absolute; left: 178px; top: 624px; width: 673px;
    font-size: 17px; line-height: 21px; color: var(--body-grey); text-align: justify;
  }
  .pill { background: var(--pill); color: var(--text-dark); }
  .explore-heading {
    position: absolute; left: 0; top: 730px; width: 406px; height: 44px;
    border-radius: 0 22px 22px 0; padding-left: 19px;
    font-size: 20px; line-height: 44px;
  }
  .topics { position: absolute; left: 18px; top: 781px; list-style: none; font-size: 17px; color: var(--text-dark); }
  .topics li { height: 29.5px; line-height: 29.5px; display: flex; align-items: center; }
  .topics li::before { content: ""; width: 10px; height: 10px; border-radius: 50%; background: var(--green-light); margin-right: 14px; }
  .audience {
    position: absolute; left: 15px; top: 910px; width: 836px;
    font-size: 15px; line-height: 21px; color: var(--body-grey); text-align: justify;
  }
  .portrait {
    position: absolute; left: 15px; top: 995px; width: 189px; height: 197px;
    background: linear-gradient(160deg, #8c8c8c, #4d4d4d);
  }
  .booking {
    position: absolute; left: 222px; top: 990px; width: 621px; height: 40px;
    border-radius: 20px; padding-left: 20px; font-size: 19px; line-height: 40px;
  }
  .booking strong, .bio strong { font-weight: 400; color: var(--text-dark); }
  .bio { position: absolute; left: 241px; top: 1046px; width: 594px; font-size: 17px; line-height: 21px; color: var(--text-dark); }
  .bio p { margin-bottom: 21px; text-align: justify; }
  .bio .web { margin-top: -2px; }
  .footer-bar { position: absolute; left: 0; bottom: 0; width: 872px; height: 22px; background: var(--green); }
</style>
</head>
<body>
<div class="flyer">
  <div class="hero-image" role="img" aria-label="Photograph of three balanced stones on raked sand"></div>
  <svg class="hero-curve" viewBox="0 0 872 240" preserveAspectRatio="none" aria-hidden="true">
    <path d="M0 240 L0 105 C180 140 330 90 470 40 C620 -10 760 0 872 60 L872 240 Z" fill="#ffffff"/>
    <path d="M0 105 C180 140 330 90 470 40 C620 -10 760 0 872 60 L872 75 C760 20 620 20 470 80 C330 140 170 190 0 165 Z" fill="var(--green-light)"/>
    <path d="M0 165 C170 190 330 140 470 80 C620 20 760 20 872 75 L872 80 C760 35 620 40 480 100 C330 170 170 225 0 222 Z" fill="var(--green)"/>
  </svg>

  <div class="headline">
    <p class="equation">Mindfulness + Kindness +<br>Compassionate Communication =</p>
    <h1 class="course-title">Gentlewise Dialogue<br>Core Course</h1>
    <p class="details">11-12 Dec<br>Linden House Centre, Edinburgh<br>(£125/100)</p>
  </div>

  <div class="brand-mark"><span class="dot"></span>Gentlewise</div>

  <p class="intro">Gentlewise Dialogue can help you increase awareness &amp; compassion in everyday speech (with yourself &amp; others), better understand your own patterns, and build resilience to challenging situations. Choose from:</p>

  <h2 class="explore-heading pill" style="font-weight:300">In this 2-day Core Course, we’ll explore:</h2>
  <ul class="topics">
    <li>Compassionate Communication;</li>
    <li>Buddhist teachings on Right Speech, loving-kindness, Right Effort, and more;</li>
    <li>Mindfulness practices;</li>
    <li>Choices available to us in our everyday speech.</li>
  </ul>

  <p class="audience">This workshop will be of interest if you’d like to improve personal and/or professional relationships.&nbsp; Open to all, best suited to those with at least 1 year’s experience with Mindfulness,&nbsp; Buddhism, or Compassionate Communication / NVC.</p>

  <div class="portrait" role="img" aria-label="Portrait photograph of the facilitator"></div>

  <p class="booking pill"><strong>Booking:</strong> Book online at TicketBloom or write <strong>marisa@gentlewise.co</strong></p>

  <div class="bio">
    <p><strong>Facilitator</strong>:&nbsp; Marisa Holloway is an experienced group facilitator, having worked with a range of organisations and presented at a number of festivals &amp; conferences.</p>
    <p>Marisa offers coaching in Gentlewise Dialogue.</p>
    <p class="web">www.gentlewise.co</p>
  </div>

  <div class="footer-bar"></div>
</div>
</body>
</html>
```